Maple Bus Card

i own a building in the bronx ny - its called "Maple 7 on 2 HDFC"i want a classy logo / business card - nothing too religuous but it is like a family there - its a large apartment building - colors i like dark red, black, medium shade of gray also reg business card stuff tel # 914-555-0173 address 4738 Larkwell Ave Bronx NY 10460 Email fijosh@aol.comslogan - " from many we are one "i can send u a picture of the building for the backside

```html
<!DOCTYPE html>
<html lang="en">
<head>
<meta charset="utf-8">
<title>Maple 7 on 2 HDFC – Business Card</title>
<link rel="stylesheet" href="https://fonts.googleapis.com/css2?family=Cinzel:wght@600&family=Open+Sans:wght@400;700&display=swap">
<style>
  :root {
    --backdrop: #2e2927;
    --card-black: #141414;
    --card-black-edge: #1d1d1d;
    --gold: #e9b41c;
    --gray: #a9a9a9;
    --gray-light: #d6d6d6;
    --rule: #6a6a6a;
    --brick: #7a3a32;
    --foliage: #3d5a2c;
    --street: #8a8d90;
  }
  * { margin: 0; padding: 0; box-sizing: border-box; }
  html, body {
    width: 1200px; height: 844px; overflow: hidden;
    background: var(--backdrop);
  }
  .stage {
    position: relative; width: 1200px; height: 844px;
    display: flex; align-items: center; justify-content: center; gap: 40px;
  }
  .card {
    position: relative; width: 540px; height: 310px;
    box-shadow: 0 10px 28px rgba(0,0,0,.45);
    overflow: hidden;
  }
  .card--front {
    background: linear-gradient(135deg, var(--card-black-edge), var(--card-black) 60%);
  }
  .brand-dot {
    position: absolute; left: 92px; top: 78px;
    width: 64px; height: 64px; border-radius: 50%;
    background: var(--gold);
  }
  .brand {
    position: absolute; left: 190px; top: 62px; width: 300px;
    text-align: center;
  }
  .brand__name {
    font-family: 'Cinzel', serif; font-weight: 600;
    font-size: 29px; letter-spacing: 1px; color: var(--gold);
    line-height: 1.1;
  }
  .brand__tag {
    display: flex; align-items: center; gap: 10px; margin-top: 4px;
  }
  .brand__tag::before, .brand__tag::after {
    content: ""; flex: 1; height: 1px; background: var(--rule);
  }
  .brand__tag span {
    font-family: 'Open Sans', sans-serif; font-weight: 700;
    font-size: 13px; color: var(--gray-light); letter-spacing: 1px;
  }
  .brand__slogan {
    margin-top: 10px;
    font-family: 'Open Sans', sans-serif; font-weight: 700;
    font-size: 15px; color: var(--gray); letter-spacing: 1px;
  }
  .contact {
    position: absolute; left: 36px; bottom: 30px;
    list-style: none;
    font-family: 'Open Sans', sans-serif; font-size: 14px; color: var(--gray-light);
  }
  .contact li { display: flex; align-items: center; gap: 8px; line-height: 24px; }
  .contact svg { width: 14px; height: 14px; fill: var(--gold); flex: none; }
  .card--back {
    background: linear-gradient(180deg, var(--brick) 0%, #8a4a40 45%, var(--foliage) 70%, var(--street) 100%);
  }
</style>
</head>
<body>
<main class="stage">
  <section class="card card--front">
    <div class="brand-dot" aria-hidden="true"></div>
    <div class="brand">
      <div class="brand__name">Maple 7 on 2</div>
      <div class="brand__tag"><span>HDFC</span></div>
      <div class="brand__slogan">FROM MANY WE ARE ONE</div>
    </div>
    <ul class="contact">
      <li>
        <svg viewBox="0 0 24 24" aria-hidden="true"><path d="M6.6 10.8a15 15 0 0 0 6.6 6.6l2.2-2.2a1 1 0 0 1 1-.25 11.4 11.4 0 0 0 3.6.57 1 1 0 0 1 1 1V20a1 1 0 0 1-1 1A17 17 0 0 1 3 4a1 1 0 0 1 1-1h3.5a1 1 0 0 1 1 1c0 1.25.2 2.45.57 3.57a1 1 0 0 1-.25 1z"/></svg>
        914-555-0173
      </li>
      <li>
        <svg viewBox="0 0 24 24" aria-hidden="true"><path d="M2 5h20v14H2z M4 7v.5l8 5 8-5V7l-8 5z" fill-rule="evenodd"/></svg>
        mavreld@quintmail.com
      </li>
      <li>
        <svg viewBox="0 0 24 24" aria-hidden="true"><path d="M12 2a7 7 0 0 0-7 7c0 5 7 13 7 13s7-8 7-13a7 7 0 0 0-7-7zm0 9.5A2.5 2.5 0 1 1 12 6.5a2.5 2.5 0 0 1 0 5z"/></svg>
        4738 Larkwell Ave Bronx NY 10460
      </li>
    </ul>
  </section>

  <section class="card card--back" role="img" aria-label="Photograph of the brick apartment building with fire escapes, trees and parked cars on the street"></section>
</main>
</body>
</html>
```